Pine Ledge Traders, LLC- Global Beverage Company with 100% Cold Chain Logistics

Hey All, My Name is Dale, I am a young business owner in a competitive export space, but my niche is that I am shipping all of my beer around the world, "100% Cold Chain". This model is more costly, but it protects the integrity of the beer itself and will give folks in foreign countries the best representation of what US Craft Beer has to offer.

I am not a branding guy and don't claim to be one, I am a salesperson first, and will be referring to all of you to create something great that will be memorable.

I am looking for a basic Business Card Design for my Craft Beer Export company. I sell US Craft Beer in several countries around the globe. Austrailia, China, Taiwan, Chile, France, New Zealand... to name a few.

I am looking for a sleek, modern, and fresh design. Quickly!

Thanks for your consideration!

Cheers,

Dale

Target Market(s)

International

Contact Information for Business Card

Dale Corrigan
Founder- Roaming Hops Guy
Dale@PineLedgeTraders.example
@RoamingHopsGuy- Instagram only
www.Pineledgetraders.example
@PineLedgeTradersAU- Instagram Only

Font styles to use
Serif

Colors
0592cd
ffffff

Requirements
Must have
• Name-
• Title-
• Email-
• Social Media Handle-
• Company Website-
Nice to have
• Nice Logo/ Images on Card
Should not have
• Tacky Beer Images

```html
<!DOCTYPE html>
<html lang="en">
<head>
<meta charset="utf-8">
<title>Pine Ledge Traders – Business Card</title>
<link rel="stylesheet" href="https://fonts.googleapis.com/css2?family=Cinzel:wght@400;500&family=Lato:wght@400&family=Arimo:wght@400&display=swap">
<style>
  :root {
    --stage: #555555;
    --card-light: #ffffff;
    --card-dark: #2b2b2b;
    --brand-blue: #0592cd;
    --map-blue: #4aa8e8;
    --ink: #333333;
    --muted: #6d6e70;
    --rule: #9a9a9a;
    --white: #ffffff;
  }
  * { margin: 0; padding: 0; box-sizing: border-box; }
  html, body { width: 1200px; height: 900px; overflow: hidden; }
  body { background: var(--stage); position: relative; font-family: "Lato", sans-serif; }

  .card {
    position: absolute;
    top: 170px;
    width: 347px;
    height: 561px;
    box-shadow: 2px 3px 6px rgba(0,0,0,0.35);
    text-align: center;
  }
  .card--front { left: 259px; background: var(--card-light); }
  .card--back  { left: 631px; background: var(--card-dark); overflow: hidden; }

  /* Front */
  .brand { position: absolute; top: 92px; left: 0; right: 0; }
  .brand__mark {
    width: 34px; height: 34px;
    margin: 0 auto 34px;
    background: var(--brand-blue);
  }
  .brand__name {
    font-family: "Cinzel", serif;
    font-weight: 500;
    font-size: 27px;
    letter-spacing: 0.5px;
    color: var(--brand-blue);
    line-height: 1;
  }
  .brand__tagline {
    margin-top: 22px;
    font-family: "Lato", sans-serif;
    font-size: 14.5px;
    letter-spacing: 2px;
    color: var(--muted);
  }

  .person { position: absolute; top: 333px; left: 0; right: 0; }
  .person__name {
    font-family: "Cinzel", serif;
    font-size: 21px;
    letter-spacing: 1px;
    color: var(--brand-blue);
  }
  .person__title { margin-top: 4px; font-size: 15px; color: var(--ink); }

  .divider { position: absolute; height: 1px; background: var(--rule); }
  .card--front .divider { top: 396px; left: 47px; width: 251px; }

  .contact { position: absolute; top: 410px; left: 0; right: 0; font-size: 15px; color: var(--ink); line-height: 21px; }
  .contact__label { color: var(--brand-blue); margin-right: 4px; }

  .social { position: absolute; top: 473px; left: 45px; right: 45px; height: 22px; display: flex; align-items: center; gap: 8px; }
  .social__line { flex: 1; height: 1px; background: var(--rule); }
  .social__dot { width: 22px; height: 22px; border-radius: 50%; background: var(--brand-blue); }
  .social__handle { position: absolute; top: 501px; left: 0; right: 0; font-size: 15px; color: var(--ink); }

  /* Back */
  .world-map {
    position: absolute; top: 0; left: 0; width: 347px; height: 392px;
    background: radial-gradient(ellipse at 65% 45%, rgba(74,168,232,0.55), rgba(74,168,232,0.18) 60%, rgba(43,43,43,0) 85%);
  }
  .back__headline {
    position: absolute; top: 405px; left: 0; right: 0;
    font-family: "Cinzel", serif;
    font-size: 18.5px;
    letter-spacing: 0.5px;
    color: var(--brand-blue);
  }
  .card--back .divider { top: 451px; left: 33px; width: 280px; background: var(--white); }
  .markets {
    position: absolute; top: 468px; left: 0; right: 0;
    font-family: "Arimo", sans-serif;
    font-size: 18px;
    line-height: 23px;
    color: var(--white);
  }
</style>
</head>
<body>
  <section class="card card--front">
    <div class="brand">
      <div class="brand__mark"></div>
      <div class="brand__name">PINE LEDGE TRADERS</div>
      <div class="brand__tagline">GLOBAL BEVERAGE COMPANY</div>
    </div>

    <div class="person">
      <div class="person__name">DALE CORRIGAN</div>
      <div class="person__title">Founder - Roaming Hops Guy</div>
    </div>

    <div class="divider"></div>

    <div class="contact">
      <div><span class="contact__label">E:</span>Dale@PineLedgeTraders.example</div>
      <div><span class="contact__label">W:</span>www.Pineledgetraders.example</div>
    </div>

    <div class="social">
      <span class="social__line"></span>
      <span class="social__dot"></span>
      <span class="social__line"></span>
    </div>
    <div class="social__handle">@RoamingHopsGuy</div>
  </section>

  <section class="card card--back">
    <div class="world-map" role="img" aria-label="Dotted world map in light blue on a charcoal background"></div>
    <div class="back__headline">100% Cold Chain Logistics</div>
    <div class="divider"></div>
    <div class="markets">
      <div>Austrailia | China | Taiwan</div>
      <div>Chile | France | New Zealand</div>
    </div>
  </section>
</body>
</html>
```